Etiketten-Design für Dankeswein
Zielgruppe
Kelvora:
Wir stellen für unsere Kunden einen Dankeswein her. Er soll eine Hommage an die Freundschaft und Partnerschaft sein.
Subtitle, could be, but perhaps not:
When we meet, anything can happen.
Name: Kelvora (evtl. Änderung auf Tarnis)
Aufgabenstellung
Das Ettikett darf auch bunt sein, aber es sollte vorallem sehr Professionell sein.
Der Wein wird rötlich sein, die Flasche weiss durchsichtig. Es werden wahrscheinlich 0,5l Flaschen.
Die Form des Ettikets, kann noch definiert werden.
Es geht um eine Homage an das Treffen von Menschen und die Freundschaft.
Kelvora
Hintergrundinfos, die eher für den Hintergrund, Einarbeitung und kleine Abbildung gedacht sind.
PLORAX: ist eine IT Firma, die von 2 Partnern gegründet wurde. Das Logo sollte mit drauf, evtl. kann man auch sich an diesen Farben orientieren.
Familie Dormak: Die Tiersymbole repräsentieren die beiden Eltern. Das geschwungene H ist das Familienzeichen. Wenn man es rotiert. ähnelt es wieder einem Schmetterling. Vielleicht kann man da grafisch etwas machen?
Das geschwungene H oder die Tiersymbole haben hohen emotionalen Wert. In dem Wappen ist das neue Familiensymbol eingearbeitet in das noch ältere Familienwappen der Familie. Prio hat das geschwungene H
Für das Ettikett gibt es leider rechtliche Pflichtangaben:
PLORAX GmbH
Lindauring 14 CH-4057 Basel
Erzeugerab füllung:D- RP 7 348 962
A.P.-Nr.7 348 962 XXXX
11,0%vol 50 cl Enthält Sulfite
Deutscher Qualitätswein – Mosel
kelvora-beispiel.eu

```html
<!DOCTYPE html>
<html lang="de">
<head>
<meta charset="utf-8">
<title>Tarnis – Etikett 2020 Rotling</title>
<link rel="stylesheet" href="https://fonts.googleapis.com/css2?family=Pinyon+Script&family=Special+Elite&family=Roboto:wght@400;500&display=swap">
<style>
  :root {
    --canvas: #ffffff;
    --label-black: #000000;
    --ink-white: #ffffff;
    --gold: #c9a84a;
  }
  html, body {
    margin: 0;
    padding: 0;
    overflow: hidden;
  }
  body {
    width: 848px;
    height: 1200px;
    background: var(--canvas);
    position: relative;
  }
  .label {
    position: absolute;
    left: 84px;
    top: 253px;
    width: 680px;
  }
  .label-main {
    position: relative;
    height: 592px;
    background: var(--label-black);
    color: var(--ink-white);
    text-align: center;
  }
  .family-mark {
    position: absolute;
    top: 62px;
    left: 0;
    right: 0;
    display: flex;
    justify-content: center;
    align-items: center;
    gap: 12px;
    font-family: "Roboto", sans-serif;
    font-weight: 500;
    font-size: 26px;
    letter-spacing: 6px;
    color: var(--gold);
  }
  .family-mark .dot {
    width: 10px;
    height: 10px;
    border-radius: 50%;
    background: var(--gold);
  }
  .wine-name {
    position: absolute;
    top: 130px;
    left: 0;
    right: 0;
    margin: 0;
    font-family: "Pinyon Script", cursive;
    font-weight: 400;
    font-size: 150px;
    line-height: 1;
  }
  .tagline {
    position: absolute;
    top: 362px;
    left: 0;
    right: 0;
    margin: 0;
    font-family: "Special Elite", monospace;
    font-size: 28px;
    line-height: 44px;
    letter-spacing: 2px;
  }
  .vintage {
    position: absolute;
    top: 528px;
    left: 0;
    right: 0;
    margin: 0;
    font-family: "Roboto", sans-serif;
    font-size: 27px;
    letter-spacing: 0.5px;
  }
  .label-band {
    margin-top: 21px;
    height: 80px;
    background: var(--label-black);
    color: var(--ink-white);
    display: flex;
    align-items: center;
    justify-content: center;
    font-family: "Roboto", sans-serif;
    font-weight: 400;
    font-size: 48px;
    letter-spacing: 1px;
  }
</style>
</head>
<body>
  <div class="label">
    <section class="label-main">
      <div class="family-mark"><span class="dot"></span>DORMAK</div>
      <h1 class="wine-name">tarnis</h1>
      <p class="tagline">WHEN WE MEET,<br>ANYTHING CAN HAPPEN</p>
      <p class="vintage">2020 ROTLING</p>
    </section>
    <div class="label-band">PLORAX</div>
  </div>
</body>
</html>
```